Business card design Needed for new logo / Construction business, home extensions and new builds

We need a business card design using our new logo files which i will attach to this project :)

We are a small construction business specialising in home extensions, new builds and property development. We are very ambitious and would appreciate professional and elegant designs for our new business card.

Very serious about using the services on MakerQuarry and recently acquired our new logo from here :)

Please get involved, i will feedback when i can as i am very busy but can respond daily, thanks

Target Market(s)

People that want to build onto their houses, new building developments or adding too their existing property

Industry/Entity Type

Construction

Contact Information for Business Card

Renwick Tolliver Construction, Lionel Ashby (Managing Director), Tel 07822254961, email - info@renwick-tolliver, www.renwick-tolliver.co.uk

Colors

Designer to choose colors to be used in the design.

Requirements
Must have
• I like a deep grey on the back please. A lot of you have provided black from and back, try mixing things up a little. The black looks cool 😎 Thanks

```html
<!DOCTYPE html>
<html lang="en">
<head>
<meta charset="utf-8">
<title>Renwick Tolliver Construction – Business Card</title>
<link rel="stylesheet" href="https://fonts.googleapis.com/css2?family=Montserrat:wght@400;500;700&display=swap">
<style>
  :root {
    --backdrop: #2b2b2d;
    --card-black: #1b1c1c;
    --deep-grey: #3a3a3e;
    --deep-grey-light: #45454a;
    --gold: #d9a93a;
    --gold-light: #f2cf72;
    --silver: #c9cacd;
    --white: #f1f1f1;
  }
  * { box-sizing: border-box; margin: 0; padding: 0; }
  html, body { width: 1200px; height: 689px; overflow: hidden; }
  body {
    background: var(--backdrop);
    font-family: "Montserrat", sans-serif;
    position: relative;
  }
  .card {
    position: absolute;
    top: 184px;
    width: 560px;
    height: 320px;
    border-radius: 18px;
    overflow: hidden;
  }
  .card--back { left: 27px; background: var(--deep-grey); }
  .card--front { left: 613px; background: var(--card-black); }

  .back-pattern {
    position: absolute; inset: 0;
    background: radial-gradient(circle at 60% 40%, var(--deep-grey-light), var(--deep-grey) 75%);
  }
  .back-brand {
    position: absolute; right: 70px; top: 110px;
    color: var(--gold); font-weight: 700; font-size: 14px; letter-spacing: 0.5px;
    display: flex; align-items: center; gap: 7px;
  }
  .brand-square { width: 10px; height: 10px; background: var(--gold); }

  .front-art { position: absolute; inset: 0; }

  .front-brand {
    position: absolute; left: 34px; top: 40px;
    color: var(--gold); font-weight: 700; font-size: 17px;
    display: flex; align-items: center; gap: 8px;
  }
  .person { position: absolute; left: 34px; top: 150px; }
  .person__name { color: var(--gold); font-weight: 700; font-size: 24px; }
  .person__role { color: var(--white); font-size: 14px; margin-top: 2px; }
  .contacts { position: absolute; left: 34px; top: 222px; list-style: none; }
  .contacts li {
    color: var(--white); font-size: 13px; line-height: 22px;
    display: flex; align-items: center; gap: 9px;
  }
  .contacts svg { width: 12px; height: 12px; fill: var(--gold); flex: none; }

  .panel-brand {
    position: absolute; right: 34px; top: 128px; width: 200px;
    text-align: center; color: var(--silver);
    font-weight: 500; font-size: 19px; line-height: 1.3;
    text-transform: uppercase; letter-spacing: 1px;
  }
</style>
</head>
<body>

<section class="card card--back" aria-label="Card back">
  <div class="back-pattern" role="img" aria-label="Faint embossed repeating brand monogram pattern on deep grey"></div>
  <div class="back-brand"><span class="brand-square"></span>Renwick Tolliver</div>
</section>

<section class="card card--front" aria-label="Card front">
  <svg class="front-art" viewBox="0 0 560 320" aria-hidden="true">
    <defs>
      <linearGradient id="goldBand" x1="0" y1="0" x2="0" y2="1">
        <stop offset="0" stop-color="#a47a22"/>
        <stop offset="0.5" stop-color="#f2cf72"/>
        <stop offset="1" stop-color="#d9a93a"/>
      </linearGradient>
      <linearGradient id="silverBand" x1="0" y1="0" x2="0" y2="1">
        <stop offset="0" stop-color="#e6e7ea"/>
        <stop offset="0.6" stop-color="#8d8e92"/>
        <stop offset="1" stop-color="#c9cacd"/>
      </linearGradient>
    </defs>
    <path d="M282,0 C258,160 330,300 440,320 L560,320 L560,0 Z" fill="url(#goldBand)"/>
    <path d="M290,0 C268,150 340,290 452,318 L560,320 L560,0 Z" fill="url(#silverBand)"/>
    <path d="M300,0 C280,150 350,282 462,312 L560,320 L560,0 Z" fill="var(--deep-grey)"/>
  </svg>

  <div class="front-brand"><span class="brand-square"></span>Renwick Tolliver</div>

  <div class="person">
    <p class="person__name">Lionel Ashby</p>
    <p class="person__role">Managing Director</p>
  </div>

  <ul class="contacts">
    <li><svg viewBox="0 0 24 24"><path d="M6.6 10.8a15 15 0 0 0 6.6 6.6l2.2-2.2a1 1 0 0 1 1-.25 11.4 11.4 0 0 0 3.6.57 1 1 0 0 1 1 1V20a1 1 0 0 1-1 1A17 17 0 0 1 3 4a1 1 0 0 1 1-1h3.5a1 1 0 0 1 1 1c0 1.25.2 2.45.57 3.57a1 1 0 0 1-.25 1z"/></svg>07822254961</li>
    <li><svg viewBox="0 0 24 24"><path d="M2 5h20v14H2z M2 5l10 8 10-8" /></svg>info@renwick-tolliver</li>
    <li><svg viewBox="0 0 24 24"><circle cx="12" cy="12" r="10"/></svg>www.renwick-tolliver.co.uk</li>
  </ul>

  <p class="panel-brand">Renwick Tolliver Construction</p>
</section>

</body>
</html>
```